Biz Card Design TVCP

New business card for a new company.
Logo was completed by a designer on ArtHarbor and looking to continue requesting additional services.
Company Name: Tidal Vector Power Consulting
Although this company is starting in Canada, we will be moving towards a global presence within the next 6 months.
Key elements to this business are as follows.
Energy Procurement
Energy Reduction Services
Demand Side Consulting
Energy Efficiency Consulting
Saving Clients Money
Helping Them Go "Green"
Managing Their Energy Requirements
Basically the goal for our company is to find the best procurement solution for our clients and reduce their energy consumption. This reduces their expenses and the amount of greenhouse gas they produce on a daily basis.
I have been in the energy footprint for the last 20 years and know that most companies are looking to "do whatever is necessary to get them to sign on the dotted line". I would prefer to walk away from a client that I can't help than to put them into a situation that they will regret for years to come. This is where the "TIDAL" part of the company name comes from.
The following is a catch phrase that encompasses what we do.
"Reducing your carbon footprint & energy bill at the same time!"
The back of the card needs to have this statement along with some sort of illustration. The back is a playground for creative ideas.
The front of the card needs the following.
Logo.
First & Last Name (Gus Marwick)
Title (Energy Warrior)
Phone Number (555) 314-2718
Fax Number (555) 271-8314
Email Address gus@tidalvectorpowerconsulting.example
Address 47 fenwick rd Toronto Ontario K4T 2P9
I want it to be a card that is remembered when any of my staff give it to a customer. It HAS to stand out.
Target Market(s)
Business Owners, Decision Makers, 30 to 65+
Industry/Entity Type
Business
Look and feel

```html
<!DOCTYPE html>
<html lang="en">
<head>
<meta charset="utf-8">
<title>Tidal Vector Power Consulting — Business Card</title>
<link rel="stylesheet" href="https://fonts.googleapis.com/css2?family=Open+Sans:ital,wght@0,400;0,600;0,700;1,600&display=swap">
<style>
  :root {
    --bg: #e9e6e1;
    --blue: #3d6db5;
    --blue-dark: #345f9f;
    --green: #2e9a3e;
    --green-light: #c3e09a;
    --green-deep: #0f8a3c;
    --ink: #5a5a5a;
    --white: #ffffff;
  }
  * { box-sizing: border-box; margin: 0; padding: 0; }
  html, body { width: 1200px; height: 900px; overflow: hidden; }
  body {
    background: var(--bg);
    font-family: "Open Sans", Arial, sans-serif;
    display: flex;
    align-items: center;
    justify-content: center;
    gap: 40px;
  }
  .card {
    position: relative;
    width: 540px;
    height: 310px;
    overflow: hidden;
    box-shadow: 0 10px 24px rgba(0,0,0,0.22);
  }

  /* Back */
  .card-back { background: var(--blue); color: var(--white); }
  .back-decoration {
    position: absolute; top: 0; right: 0; width: 190px; height: 200px;
    background: radial-gradient(ellipse at 70% 40%, rgba(255,255,255,0.55), rgba(255,255,255,0.08) 70%, rgba(255,255,255,0) 80%);
  }
  .back-name {
    position: absolute; left: 34px; top: 34px; width: 320px;
    font-weight: 700; font-size: 21px; line-height: 1.15; color: var(--white);
  }
  .service-list {
    position: absolute; left: 34px; top: 102px; list-style: none;
    font-size: 13.5px; line-height: 21px;
  }
  .service-list li { display: flex; align-items: center; gap: 10px; }
  .service-list li::before {
    content: ""; width: 9px; height: 9px; border-radius: 50%; background: var(--white);
  }
  .back-band {
    position: absolute; left: 0; right: 0; bottom: 0; height: 40px;
    background: var(--blue-dark);
    display: flex; align-items: center; justify-content: center;
  }
  .tagline { font-weight: 600; font-style: italic; font-size: 13px; color: var(--white); }

  /* Front */
  .card-front { background: var(--white); }
  .front-decoration {
    position: absolute; left: 0; bottom: 0; width: 150px; height: 150px;
    background: radial-gradient(ellipse at 30% 60%, rgba(74,170,74,0.75), rgba(150,210,120,0.35) 55%, rgba(255,255,255,0) 75%);
  }
  .front-logo {
    position: absolute; left: 150px; top: 62px;
    display: flex; align-items: center; gap: 10px;
  }
  .logo-dot { width: 22px; height: 22px; border-radius: 50%; background: var(--green); }
  .logo-name { font-weight: 700; font-size: 17px; color: var(--blue); }
  .contact {
    position: absolute; right: 30px; top: 108px;
    font-size: 12.5px; line-height: 20px; color: var(--ink);
  }
  .contact .label { color: var(--green); }
  .contact .email { margin-top: 10px; }
  .person {
    position: absolute; left: 150px; top: 190px;
  }
  .person-name { font-weight: 700; font-size: 19px; color: var(--green); }
  .person-title { font-weight: 600; font-size: 13px; color: var(--blue); }
  .address { margin-top: 4px; font-size: 13px; line-height: 18px; color: var(--ink); }
  .front-band {
    position: absolute; left: 150px; right: 0; bottom: 0; height: 44px;
    background: linear-gradient(90deg, var(--green-light), var(--green) 60%, var(--green-deep));
    display: flex; align-items: center; justify-content: center;
  }
</style>
</head>
<body>
  <section class="card card-back">
    <div class="back-decoration" role="img" aria-label="Large white leaf artwork"></div>
    <h1 class="back-name">Tidal Vector Power Consulting</h1>
    <ul class="service-list">
      <li>Energy Procurement</li>
      <li>Energy Reduction Services</li>
      <li>Demand Side Consulting</li>
      <li>Energy Efficiency Consulting</li>
      <li>Saving Clients Money</li>
      <li>Helping Them Go "Green"</li>
      <li>Managing Their Energy Requirements</li>
    </ul>
    <div class="back-band">
      <p class="tagline">"Reducing your carbon footprint &amp; energy bill at the same time!"</p>
    </div>
  </section>

  <section class="card card-front">
    <div class="front-decoration" role="img" aria-label="Green leaf artwork"></div>
    <div class="front-logo">
      <span class="logo-dot"></span>
      <span class="logo-name">Tidal Vector Power Consulting</span>
    </div>
    <div class="contact">
      <p><span class="label">Phone :</span> (555) 314-2718</p>
      <p><span class="label">Fax :</span> (555) 271-8314</p>
      <p class="email">gus@tidalvectorpowerconsulting.example</p>
    </div>
    <div class="person">
      <p><span class="person-name">Gus Marwick</span> <span class="person-title">I Energy Warrior</span></p>
      <p class="address">47 fenwick rd Toronto<br>Canada K4T 2P9</p>
    </div>
    <div class="front-band">
      <p class="tagline">"Reducing your carbon footprint &amp; energy bill at the same time!"</p>
    </div>
  </section>
</body>
</html>
```